Website for a company offering full serivce charging solutions for electric cars

The company "tanu-werk" (english: "tanu-works") offering all-in-one-solutions for charging infrastructure for electric mobility.

There are four products:
1- Wallboxes for single-family homes
2- Solutions for property devloper/-management for property parking space
3- All-in-one-charging solution for municipalities/communities
4- Solutions for tourism/hotels/holiday appartments

The Website structure:
1. Main Page
2.1. Product Page Single Homes
2.2. Product Page Property Management / Parking
2.3. Product Page Municipality
2.4. Product Page Tourism
3. Contact Form / Request for information
4. Imprint / Legal

The Website should be built on Wordpress with a powerful possibility to simply add/modify specific landing pages.

We would like you to implement the website later and also maintain it if possible, but we would be able to do minor modifications by ourselfs (for A/B-Testing)

The website should be clear and simple, easy to understand.
Target group is mainly B2C without deeper knowledge of that topic.

It should suggest, that we will provide a very simple way to get the charging infrastructure done.

We need a contact form, maybe we will use Hubspot later.

Attached you will find a draft of the main page and a landing page (for 2.2) - it is just the content, please ignore the design. We would love to let you create a suitable design.
Also you will find some drafts a bit different for the same story.

I added also a few stock photos, but they don't need to be used! If you have better ideas, you are welcome!

Industry/Entity Type

Charging/Electric mobility

Number of Pages Required

2 page

Font styles to use
Sans Serif

Requirements
Must have
• Based on Wordpress, and the designer should be able to implement it on Wordpress on a later step

```html
<!DOCTYPE html>
<html lang="de">
<head>
<meta charset="utf-8">
<title>tanu-werk.de – Ladeinfrastruktur für Elektromobilität</title>
<link href="https://fonts.googleapis.com/css2?family=Righteous&family=Lexend:wght@400;500;600&family=Questrial&display=swap" rel="stylesheet">
<style>
:root{
  --magenta:#e6119b;
  --purple:#8b4fd0;
  --navy:#1c2940;
  --deep:#111a2b;
  --band:#26365a;
  --foot:#1b2539;
  --white:#ffffff;
  --muted:#d7dbe6;
}
*{margin:0;padding:0;box-sizing:border-box}
html,body{width:1200px;height:4065px;overflow:hidden}
body{position:relative;background:var(--deep);font-family:"Questrial",sans-serif;color:var(--white)}
.abs{position:absolute}

/* header */
.site-header{left:0;top:0;width:1200px;height:87px;background:var(--white)}
.brand{left:126px;top:26px;display:flex;align-items:center;gap:10px;font-family:"Lexend",sans-serif;font-weight:500;font-size:22px;color:#2a2a3a}
.brand-dot{width:30px;height:30px;border-radius:50%;background:var(--magenta)}
.main-nav{left:410px;top:34px;display:flex;gap:21px;font-family:"Lexend",sans-serif;font-size:13px;color:#2b2b3b}
.main-nav .active{border-bottom:2px solid var(--purple);padding-bottom:6px}
.phone-btn{left:881px;top:25px;width:194px;height:38px;border-radius:19px;background:linear-gradient(90deg,var(--magenta),var(--purple));display:flex;align-items:center;gap:8px;padding-left:6px;font-family:"Lexend",sans-serif;font-weight:600;font-size:11.5px;white-space:nowrap}
.phone-btn .ico{width:28px;height:28px;border-radius:50%;background:var(--white);display:flex;align-items:center;justify-content:center;flex:none}

/* hero */
.hero{left:0;top:87px;width:1200px;height:562px;background:linear-gradient(180deg,#5b6774 0%,#7b7d7b 45%,#a59a8a 70%,#55544f 100%)}
.hero-title{left:0;top:210px;width:1200px;text-align:center;font-family:"Righteous",sans-serif;font-weight:400;font-size:38px;line-height:50px;text-shadow:0 2px 8px rgba(0,0,0,.4)}
.btn-fill{border-radius:22px;background:linear-gradient(90deg,var(--magenta),#c8179f);font-family:"Lexend",sans-serif;font-weight:600;font-size:13px;display:flex;align-items:center;justify-content:center}
.hero-btn{left:492px;top:336px;width:215px;height:40px}

/* partner */
.partner{left:0;top:649px;width:1200px;height:646px;background:var(--navy)}
.photo{border-radius:18px}
.ph-a{left:245px;top:740px;width:228px;height:228px;background:linear-gradient(160deg,#e8a23a,#8a5a3a 60%,#3a3030)}
.ph-b{left:163px;top:898px;width:189px;height:217px;background:linear-gradient(150deg,#f2f4f8,#9fb5d8 55%,#2f6fe0)}
.ph-c{left:359px;top:975px;width:227px;height:228px;background:linear-gradient(150deg,#e6eef5,#6ea0c4 50%,#1d3a5a)}
.collage-line{left:222px;top:1140px}
.partner-text{left:606px;top:735px;width:436px}
.h2{font-family:"Lexend",sans-serif;font-weight:500;font-size:34px;line-height:42px}
.lead{margin-top:18px;color:var(--magenta);font-family:"Lexend",sans-serif;font-size:16px;line-height:24px}
.partner-text p.body{margin-top:10px;font-size:12.5px;line-height:24px;color:var(--muted)}
.btn-outline{left:606px;top:1175px;width:204px;height:36px;border:2px solid var(--magenta);border-radius:18px;font-family:"Lexend",sans-serif;font-weight:600;font-size:11.5px;display:flex;align-items:center;justify-content:center}

/* services */
.services{left:0;top:1295px;width:1200px;height:1926px;background:var(--deep)}
.snake{left:0;top:0}
.h3{font-family:"Lexend",sans-serif;font-weight:500;font-size:34px;line-height:40px}
.ticks{list-style:none;font-size:12.5px;line-height:24px;color:var(--muted)}
.ticks li{position:relative;padding-left:25px;margin-bottom:8px}
.ticks li::before{content:"";position:absolute;left:0;top:6px;width:11px;height:11px;border:1.5px solid var(--magenta);border-radius:50%}
.ticks li::after{content:"";position:absolute;left:3px;top:8px;width:6px;height:3px;border-left:1.5px solid var(--magenta);border-bottom:1.5px solid var(--magenta);transform:rotate(-45deg)}
.ticks ul{list-style:none;margin-top:8px}
.ticks ul li{margin-left:6px}
.private-h{left:163px;top:1385px}
.private-list{left:163px;top:1447px;width:400px}
.business-h{left:597px;top:1845px}
.business-list{left:597px;top:1906px;width:415px}
.business-more{left:163px;top:2302px;width:435px}
.municipal-h{left:625px;top:2718px}
.municipal-list{left:625px;top:2780px;width:415px}

/* cta band */
.cta{left:0;top:3221px;width:1200px;height:355px;background:linear-gradient(90deg,#3a4b6d,var(--band) 55%,#22304d)}
.cta-img{left:0;top:3230px;width:474px;height:340px;background:linear-gradient(90deg,#d7dde4,#9aa5b2 50%,#e9ecef 80%,rgba(0,0,0,0));border-radius:0 40px 40px 0}
.cta-title{left:567px;top:3305px;width:450px;font-family:"Righteous",sans-serif;font-weight:400;font-size:35px;line-height:41px}
.cta-btn{left:567px;top:3450px;width:243px;height:41px}

/* footer */
.footer{left:0;top:3576px;width:1200px;height:489px;background:var(--foot)}
.foot-brand{left:0;top:3652px;width:1200px;display:flex;justify-content:center;align-items:center;gap:14px;font-family:"Lexend",sans-serif;font-weight:500;font-size:36px}
.foot-brand .brand-dot{width:44px;height:44px}
.foot-links{left:0;top:3747px;width:1200px;display:flex;justify-content:center;gap:54px;font-family:"Lexend",sans-serif;font-size:12.5px}
.contact-box{left:161px;top:3786px;width:876px;height:119px;border-radius:10px;background:linear-gradient(90deg,var(--magenta),#b02bb8 50%,var(--purple));display:flex;padding:26px 0 0 26px}
.contact-item{display:flex;gap:14px;width:300px}
.contact-item .ic{width:34px;height:34px;border-radius:50%;background:var(--deep);flex:none;display:flex;align-items:center;justify-content:center}
.contact-item b{display:block;font-family:"Lexend",sans-serif;font-weight:500;font-size:14px;line-height:20px}
.contact-item span{font-size:13px;line-height:20px}
.copyright{left:0;top:3950px;width:1200px;text-align:center;font-family:"Lexend",sans-serif;font-size:12.5px}
.social{left:527px;top:3989px;display:flex;gap:18px}
.social span{width:36px;height:36px;border-radius:50%;background:var(--magenta)}
.bottom-bar{left:0;top:4060px;width:1200px;height:5px;background:var(--magenta)}
</style>
</head>
<body>

<header class="abs site-header">
  <div class="abs brand"><span class="brand-dot"></span>tanu-werk.de</div>
  <nav class="abs main-nav">
    <span class="active">Lösungen</span><span>Unternehmen</span><span>Dienstleistungen</span><span>Karriere</span><span>Kontakt</span>
  </nav>
  <div class="abs phone-btn"><span class="ico"><svg width="14" height="14" viewBox="0 0 24 24"><path fill="#b5179e" d="M6.6 10.8a15 15 0 006.6 6.6l2.2-2.2c.3-.3.7-.4 1-.2 1.1.4 2.3.6 3.6.6.6 0 1 .4 1 1V20c0 .6-.4 1-1 1A17 17 0 013 4c0-.6.4-1 1-1h3.5c.6 0 1 .4 1 1 0 1.3.2 2.5.6 3.6.1.3 0 .7-.2 1z"/></svg></span>0800 555 0199 (Zollfrei)</div>
</header>

<section class="abs hero" role="img" aria-label="Foto: moderne Villa in der Abenddämmerung mit weißem Elektroauto an einer Ladesäule"></section>
<h1 class="abs hero-title">All-in-One-Lösungen Für Ladeinfrastruktur<br>Für Elektromobilität Anzubieten.</h1>
<div class="abs btn-fill hero-btn">Kontaktiere Uns Heute</div>

<section class="abs partner"></section>
<div class="abs photo ph-a" role="img" aria-label="Foto: Frau mit Smartphone beim Laden ihres Autos im Sonnenuntergang"></div>
<div class="abs photo ph-b" role="img" aria-label="Foto: Ladestecker an einer blau leuchtenden Wallbox"></div>
<div class="abs photo ph-c" role="img" aria-label="Foto: Hand steckt Ladekabel in ein Elektroauto"></div>
<svg class="abs collage-line" width="140" height="10" viewBox="0 0 140 10"><defs><linearGradient id="lg" gradientUnits="userSpaceOnUse" x1="0" y1="0" x2="140" y2="0"><stop offset="0" stop-color="#e6119b"/><stop offset="1" stop-color="#8b4fd0"/></linearGradient></defs><path d="M0 5 H140" stroke="url(#lg)" stroke-width="5" fill="none"/></svg>
<div class="abs partner-text">
  <h2 class="h2">tanu-werk ist Ihr Partner</h2>
  <p class="lead">wenn das Laden nicht nur einfach, sondern die Umsetzung auch aus einer Hand kommen soll</p>
  <p class="body">Wir bieten Lösungen sowohl für Privatkunden, Geschäftskunden als auch Kommunen an, die schnell, fair und ohne Eigenleistung zu einer smarten Ladelösung für E-Fahrzeuge kommen möchten.</p>
  <p class="body">Von der Beratung, über die Installation, Inbetriebnahme bis zur Abrechnung und Wartung bekommen Sie bei tanu-werk alles aus einer Hand. Auf Wunsch vermieten wir auch die Ladetechnik und übernehmen im gewerblichen Bereich die direkte Abrechnung mit dem Nutzer. Für Kommunen bieten wir den kostenfreien Full-Service an und beteiligen die Gemeinden an der Nutzung der Infrastruktur.</p>
  <p class="body">Fragen Sie uns nach der auf Ihre individuellen Bedürfnisse zugeschnittenen Lösung:</p>
</div>
<div class="abs btn-outline">Kontaktieren Sie uns heute</div>

<section class="abs services"></section>
<svg class="abs snake" width="1200" height="4065" viewBox="0 0 760 2574">
  <defs>
    <linearGradient id="sg" x1="0" y1="0" x2="1" y2="0"><stop offset="0" stop-color="#e6119b"/><stop offset="1" stop-color="#8b4fd0"/></linearGradient>
    <linearGradient id="p1" x1="0" y1="0" x2="1" y2="1"><stop offset="0" stop-color="#2a3040"/><stop offset=".6" stop-color="#7a5a48"/><stop offset="1" stop-color="#d3222c"/></linearGradient>
    <linearGradient id="p2" x1="0" y1="0" x2="1" y2="1"><stop offset="0" stop-color="#c9ced4"/><stop offset=".5" stop-color="#f4f4f2"/><stop offset="1" stop-color="#4a4f58"/></linearGradient>
    <linearGradient id="p3" x1="0" y1="0" x2="1" y2="1"><stop offset="0" stop-color="#8da2bb"/><stop offset=".5" stop-color="#d8e0ea"/><stop offset="1" stop-color="#5f7590"/></linearGradient>
    <linearGradient id="p4" x1="0" y1="0" x2="1" y2="1"><stop offset="0" stop-color="#1f3f8a"/><stop offset=".5" stop-color="#e7753a"/><stop offset="1" stop-color="#cfd4da"/></linearGradient>
  </defs>
  <path d="M527 860 A143 143 0 0 1 527 1146 L232 1146 A140 140 0 0 0 232 1426 L527 1426 A140 140 0 0 1 527 1706 L232 1706 A141 141 0 0 0 232 1988 L680 1988 Q695 1988 695 1972 L695 1915" stroke="url(#sg)" stroke-width="3.5" fill="none"/>
  <circle cx="695" cy="1910" r="6" fill="#e6119b"/>
  <circle cx="527" cy="1003" r="132" fill="url(#p1)" role="img" aria-label="Foto: lächelnde Frau steckt Ladekabel in ein rotes Auto"/>
  <circle cx="232" cy="1286" r="132" fill="url(#p2)" role="img" aria-label="Foto: weiße Ladesäule mit Stecker neben parkenden Autos"/>
  <circle cx="527" cy="1566" r="132" fill="url(#p3)" role="img" aria-label="Illustration: Ladesäulen und transparentes Elektroauto auf einem Parkplatz"/>
  <circle cx="232" cy="1847" r="132" fill="url(#p4)" role="img" aria-label="Foto: blaues Elektroauto mit orangefarbenem Ladekabel an einer Ladesäule"/>
</svg>

<h3 class="abs h3 private-h">als Privatkunde</h3>
<ul class="abs ticks private-list">
  <li>Bestandsanalyse mit umfangreicher Beratung über die Möglichkeiten der Umsetzung</li>
  <li>Prüfung und Übernahme der Anmeldung verfügbarer Fördermöglichkeiten</li>
  <li>Auswahl an smarten Wallbox Lösungen, passend für Ihr Fahrzeug und Ihre Bedürfnisse</li>
  <li>Installation inkl. aller notwendigen Materialien und Tätigkeiten (Durchbrüche, Erdarbeiten, etc.)</li>
  <li>Inbetriebnahme und Einweisung in die Ladetechnik</li>
  <li>Jährlich technische Wartung nach DGUV3</li>
  <li>Reparaturservice, unter Berücksichtigung der geltenden Garantie Ansprüche</li>
</ul>

<h3 class="abs h3 business-h">als Geschäftskunde</h3>
<ul class="abs ticks business-list">
  <li>Durchführung einer individuellen Bedarfsanalyse inkl. Ermittlung der Anforderungen für:
    <ul>
      <li>Haus- und Immobilienverwaltungen</li>
      <li>Dienstleistungs- und Handelsunternehmen</li>
      <li>Hotel und Beherbergungsbetriebe</li>
      <li>Parkraum- und Parkhausbetreiber</li>
      <li>Tourismus, Sport- und Freizeiteinrichtungen</li>
    </ul>
  </li>
  <li>Planung und Projektierung des Installationsaufwands inkl. Materialverbrauch</li>
  <li>Leasing oder Kauf der Hardware</li>
</ul>
<ul class="abs ticks business-more">
  <li>Normgerechte Installation der Ladeinfrastruktur inkl. Durchbruch-, Brandschutz- und Erdarbeiten</li>
  <li>Leasing oder Kauf der Hardware</li>
  <li>Bei Bestandsbauten Integration der Ladeinfrastruktur in die Gebäudesystemtechnik und ggf. Anpassung des Netzanschlusses</li>
  <li>Inbetriebnahme der Anlage inkl. Prüf- und Messprotokollen</li>
  <li>Wiederkehrende technische Prüfung der Anlage nach DGUV 3</li>
  <li>Austausch und Reparatur Service</li>
  <li>Unterstützung bei der mtl. Nutzungsabrechnung und Einbindung in Ihre vorhandene Abrechnungssysteme</li>
  <li>ODER direkte Abrechnung mit den Nutzern</li>
</ul>

<h3 class="abs h3 municipal-h">als Kommune</h3>
<ul class="abs ticks municipal-list">
  <li>Konzeptionierung möglicher Ladeinfrastrukturen innerhalb Ihrer Gemeinde</li>
  <li>Planung und Projektsteuerung inkl. sämtlicher behördlicher Genehmigungsverfahren und Beantragung von Fördermitteln</li>
  <li>Fachgerechte Installation und Inbetriebnahme</li>
  <li>Regelmäßige Wartung gemäß Vorschrif</li>
  <li>Reparatur und Kundenservice</li>
  <li>Direkte Abrechnung mit dem Nutzer</li>
  <li>Beteiligung der Gemeinde am Umsatz</li>
  <li>Möglichkeit der Integration von Bonusprogrammen, mit denen der lokale Einzelhandel beworben wird</li>
</ul>

<section class="abs cta"></section>
<div class="abs cta-img" role="img" aria-label="Foto: weißes Elektroauto an einer freistehenden Ladesäule"></div>
<h2 class="abs cta-title">Werden Sie unser Partner oder Gastgeber der Ladestation</h2>
<div class="abs btn-fill cta-btn">Kontaktieren Sie uns heute</div>

<footer class="abs footer"></footer>
<div class="abs foot-brand"><span class="brand-dot"></span>tanu-werk.de</div>
<nav class="abs foot-links"><span>AGB</span><span>Datenschutzerklärung</span><span>Impressum</span><span>Kontakt</span><span>Karriere</span><span>FAQs</span></nav>
<div class="abs contact-box">
  <div class="contact-item"><span class="ic"><svg width="14" height="16" viewBox="0 0 24 24"><path fill="#fff" d="M12 2a7 7 0 00-7 7c0 5 7 13 7 13s7-8 7-13a7 7 0 00-7-7zm0 9.5A2.5 2.5 0 1112 6.5a2.5 2.5 0 010 5z"/></svg></span><div><b>Ein Kleid</b><span>Ladeweg 7, 80331 Musterstadt,<br>Bayern</span></div></div>
  <div class="contact-item"><span class="ic"><svg width="14" height="14" viewBox="0 0 24 24"><path fill="#fff" d="M6.6 10.8a15 15 0 006.6 6.6l2.2-2.2c.3-.3.7-.4 1-.2 1.1.4 2.3.6 3.6.6.6 0 1 .4 1 1V20c0 .6-.4 1-1 1A17 17 0 013 4c0-.6.4-1 1-1h3.5c.6 0 1 .4 1 1 0 1.3.2 2.5.6 3.6.1.3 0 .7-.2 1z"/></svg></span><div><b>Anruf</b><span>0800 555 0199 (Zollfrei)</span></div></div>
  <div class="contact-item"><span class="ic"><svg width="14" height="12" viewBox="0 0 24 20"><path fill="#fff" d="M2 2h20v16H2z M2 2l10 8 10-8" stroke="#111a2b" stroke-width="1.5"/></svg></span><div><b>Email</b><span>info@tanu-werk.de</span></div></div>
</div>
<p class="abs copyright">Urheberrecht © 2022 tanu-werk.de. Alle Rechte vorbehalten.</p>
<div class="abs social"><span></span><span></span><span></span></div>
<div class="abs bottom-bar"></div>

</body>
</html>
```